Tech Website

1. Overview
Prism48, formally named LumoVista, is a pioneer in computer vision technology and machine learning. Based out of Santa Clara, California, Prism48 is at the forefront of the User Interface revolution; building technology architecture that grants devices with the aptitude to respond to emotional detection, gaze tracking, facial recognition, age and gender identification and gaming interaction. Winner of the Mobile Track at NOVA Founders Sprint 2012, Prism48 has developed the next generation of consumer behaviour analytics. Prism48 software solutions are scalable across various platforms including mobile phone, tablets, PC and SmartTV.
Updates

Good day, 

Please see the update to our brief - there is a PDF of the type of format and design we are looking for.  It shows each page - Landing, Technology, Product, Press and Company.

Thank you for your designs

Regards,

Target Market(s)

Target market - A mix of enterprise and consumer audiences, targeting the need for the technology in the living room space

Industry/Entity Type

Architecture

Requirements
Must have
• Design preferences - Easy to navigate, modern with sleek feel, trendy, tech saavy, using cube as a consistent element/theme. colours are not determined, but parrot green was one idea with 2 additional underlying colours. keys words like user interface revolution or sense recognition are good sources to draw inspiration.

Landing page will have a video - illustrating different uses of technology

Technical Specs - Landing page, 6 tabs/subpages, and each subpage may have 1 or 2 additional pages. Coding will be necessary, not that much at the beginning stages.

```html
<!DOCTYPE html>
<html lang="en">
<head>
<meta charset="utf-8">
<title>Prism48 — Sense Recognition Technology</title>
<link rel="stylesheet" href="https://fonts.googleapis.com/css2?family=Oswald:wght@400;500&family=Ubuntu:wght@400;500&family=PT+Sans:wght@400;700&family=Courgette&display=swap">
<style>
  :root {
    --page-bg: #eeece2;
    --sheet: #fcfaf6;
    --white: #ffffff;
    --ink: #1c1c1c;
    --body-text: #4a4a4a;
    --nav-text: #3d4a12;
    --green-light: #b9df2c;
    --green-mid: #9bc81a;
    --green-dark: #78a80c;
    --green-script: #7aa614;
    --frame-shadow: rgba(0,0,0,0.22);
    --button-top: #4a4a4a;
    --button-bottom: #0c0c0c;
    --badge-fill: #dfe6ec;
  }
  * { box-sizing: border-box; margin: 0; padding: 0; }
  html, body { width: 1200px; height: 1040px; overflow: hidden; }
  body {
    background: var(--page-bg);
    font-family: "PT Sans", sans-serif;
    position: relative;
  }
  .brand {
    position: absolute; left: 94px; top: 30px;
    font-family: "Ubuntu", sans-serif; font-weight: 500;
    font-size: 42px; color: var(--ink);
  }
  .main-nav {
    position: absolute; left: 558px; top: 39px; height: 44px;
    display: flex; border-radius: 4px; overflow: hidden;
    background: linear-gradient(var(--green-light), var(--green-dark));
    box-shadow: 0 8px 8px -4px rgba(0,0,0,0.25);
  }
  .main-nav a {
    font-family: "Ubuntu", sans-serif; font-weight: 500; font-size: 17px;
    color: var(--nav-text); text-decoration: none;
    display: flex; align-items: center; justify-content: center;
    border-right: 1px solid rgba(255,255,255,0.35);
  }
  .main-nav a:last-child { border-right: 0; }
  .sheet {
    position: absolute; left: 75px; top: 109px; width: 1049px; height: 931px;
    background: var(--sheet);
    box-shadow: 0 0 3px rgba(0,0,0,0.08);
  }
  .hero {
    position: absolute; left: 75px; top: 126px; width: 1049px; height: 386px;
    background: var(--white);
    box-shadow: 0 2px 4px var(--frame-shadow);
  }
  .hero-title {
    position: absolute; left: 24px; top: 38px;
    font-family: "Ubuntu", sans-serif; font-weight: 400; font-size: 35px; color: var(--ink);
    text-shadow: 1px 1px 1px rgba(0,0,0,0.2);
  }
  .hero-intro {
    position: absolute; left: 29px; top: 96px; width: 372px;
    font-family: "Ubuntu", sans-serif; font-size: 16px; line-height: 24px; color: var(--ink);
  }
  .read-more {
    position: absolute; left: 30px; top: 267px; width: 166px; height: 47px;
    background: linear-gradient(var(--button-top), var(--button-bottom));
    border-radius: 2px; color: var(--white);
    font-family: "Ubuntu", sans-serif; font-size: 23px;
    display: flex; align-items: center; justify-content: center;
    box-shadow: 0 1px 2px rgba(0,0,0,0.4);
  }
  .video-frame {
    position: absolute; left: 458px; top: 8px; width: 552px; height: 370px;
    background: var(--white); padding: 5px;
    box-shadow: 0 1px 4px var(--frame-shadow);
  }
  .video-still {
    width: 100%; height: 100%;
    background: linear-gradient(135deg, #6e5a3e 0%, #2c3a52 45%, #4d6b93 60%, #7a7f86 100%);
    position: relative;
  }
  .play-btn { position: absolute; left: 50%; top: 50%; transform: translate(-50%,-50%); }
  .carousel-arrow { position: absolute; top: 612px; }
  .thumb {
    position: absolute; top: 538px; width: 317px; height: 167px; border-radius: 3px;
    box-shadow: 0 1px 2px rgba(0,0,0,0.2);
  }
  .thumb .play-btn { width: 30px; height: 30px; }
  .thumb-expo { left: 102px; background: linear-gradient(135deg, #8f8c90, #4d5a6a 55%, #c9c3c4); }
  .thumb-portrait { left: 440px; background: linear-gradient(180deg, #5d6f92, #4c5a7e 60%, #6b6a4b); }
  .thumb-racing { left: 778px; background: linear-gradient(135deg, #5b6b7c, #2b2b2e 50%, #8a7a6c); }
  .testimonial-title {
    position: absolute; left: 88px; top: 728px;
    font-family: "Courgette", cursive; font-weight: 400; font-size: 28px; color: var(--green-script);
  }
  .testimonial-text {
    position: absolute; left: 88px; top: 771px; width: 745px;
    font-size: 13.5px; line-height: 19.6px; color: var(--body-text);
  }
  .testimonial-text p + p { margin-top: 19.6px; }
  .event-badge {
    position: absolute; left: 869px; top: 731px; width: 240px; height: 142px;
    background: var(--white); border-radius: 4px;
    box-shadow: 0 1px 4px var(--frame-shadow);
    padding: 14px;
  }
  .event-badge-shape { width: 100%; height: 100%; background: var(--badge-fill); border-radius: 3px; }
  .featured {
    position: absolute; left: 87px; top: 901px; width: 749px; height: 71px;
    background: var(--white); border: 1px solid #d6d6d6; border-radius: 5px;
    display: flex; overflow: hidden;
  }
  .featured-label {
    width: 104px; height: 100%;
    background: linear-gradient(var(--green-light), var(--green-dark));
    color: var(--white); font-family: "Oswald", sans-serif; font-size: 18px;
    display: flex; align-items: center; justify-content: center;
  }
  .featured-list {
    flex: 1; display: flex; align-items: center; justify-content: space-around;
    list-style: none; padding: 0 10px;
  }
  .featured-list li {
    font-family: "PT Sans", sans-serif; font-weight: 700; font-size: 19px; color: #5a5a5a;
  }
  .subscribe {
    position: absolute; left: 871px; top: 901px; width: 240px; height: 71px;
    background: linear-gradient(var(--green-light), var(--green-dark));
    border-radius: 4px; box-shadow: 0 1px 3px rgba(0,0,0,0.25);
    font-family: "Oswald", sans-serif;
  }
  .subscribe-small { position: absolute; left: 21px; top: 8px; font-size: 17px; color: #eef7c4; }
  .subscribe-big { position: absolute; left: 21px; top: 26px; font-size: 31px; color: #1e2a06; line-height: 40px; }
  .subscribe-big span { font-size: 16px; color: #eef7c4; }
  .subscribe-icon { position: absolute; right: 16px; top: 15px; }
  .site-footer {
    position: absolute; left: 75px; top: 992px; width: 1049px; height: 48px;
    background: linear-gradient(var(--green-light), var(--green-dark));
    color: var(--white); font-size: 13px;
    display: flex; align-items: center; padding-left: 14px;
  }
</style>
</head>
<body>
  <header>
    <div class="brand">Prism48</div>
    <nav class="main-nav">
      <a href="#" style="width:98px">Home</a>
      <a href="#" style="width:137px">Technology</a>
      <a href="#" style="width:111px">Product</a>
      <a href="#" style="width:93px">Press</a>
      <a href="#" style="width:126px">Company</a>
    </nav>
  </header>

  <div class="sheet"></div>

  <section class="hero">
    <h1 class="hero-title">Welcome to Prism 48</h1>
    <p class="hero-intro">Lorem ipsum dolor sit amet, consectetur adipiscing elit. Aliquam sodales lacus at turpis scelerisque eu ullamcorper enim mattis. Quisque ultrices, neque et blandit rhoncus, ante magna commodo nibhmattis nulla tortor id magna. In et odio id leo viverra interdum.</p>
    <a class="read-more">Read More</a>
    <div class="video-frame">
      <div class="video-still" role="img" aria-label="Video still: a hand touching a tablet showing a desktop with photo folders">
        <svg class="play-btn" width="90" height="90" viewBox="0 0 90 90">
          <circle cx="45" cy="45" r="45" fill="rgba(50,50,50,0.75)"/>
          <polygon points="36,26 64,45 36,64" fill="#e6e6e6"/>
        </svg>
      </div>
    </div>
  </section>

  <svg class="carousel-arrow" style="left:78px" width="22" height="24" viewBox="0 0 22 24"><polyline points="18,2 6,12 18,22" fill="none" stroke="#111" stroke-width="5"/></svg>
  <div class="thumb thumb-expo" role="img" aria-label="Video still: visitors trying a screen demo at a trade booth">
    <svg class="play-btn" viewBox="0 0 30 30"><circle cx="15" cy="15" r="15" fill="rgba(40,40,40,0.75)"/><polygon points="12,8 22,15 12,22" fill="#ddd"/></svg>
  </div>
  <div class="thumb thumb-portrait" role="img" aria-label="Video still: face detection demo outdoors">
    <svg class="play-btn" viewBox="0 0 30 30"><circle cx="15" cy="15" r="15" fill="rgba(40,40,40,0.75)"/><polygon points="12,8 22,15 12,22" fill="#ddd"/></svg>
  </div>
  <div class="thumb thumb-racing" role="img" aria-label="Video still: hands holding a tablet running a racing game">
    <svg class="play-btn" viewBox="0 0 30 30"><circle cx="15" cy="15" r="15" fill="rgba(40,40,40,0.75)"/><polygon points="12,8 22,15 12,22" fill="#ddd"/></svg>
  </div>
  <svg class="carousel-arrow" style="left:1100px;top:607px" width="22" height="24" viewBox="0 0 22 24"><polyline points="4,2 16,12 4,22" fill="none" stroke="#111" stroke-width="5"/></svg>

  <section>
    <h2 class="testimonial-title">Testimonial</h2>
    <div class="testimonial-text">
      <p>Lorem ipsum dolor sit amet, consectetur adipisicing elit, sed do eiusmod tempor incididunt ut labore et dolore magna aliqua. Ut enim ad minim veniam, quis nostrud exercitation ullamco laboris nisi ut aliquip ex ea commodo consequat. Duis aute irure dolor in reprehenderit in voluptate velit esse cillum dolore eu fugiat nulla pariatur.</p>
      <p>Exercitation ullamco laboris nisi ut aliquip ex ea commodo consequat duis aute irure dolor.</p>
    </div>
  </section>

  <aside class="event-badge">
    <div class="event-badge-shape" role="img" aria-label="Trade show invitation badge"></div>
  </aside>

  <section class="featured">
    <div class="featured-label">FEATURED</div>
    <ul class="featured-list">
      <li>Northfield Tech</li>
      <li>Yonder</li>
      <li>Pixelwire</li>
      <li>Newsline Daily</li>
      <li>Circuit Journal</li>
    </ul>
  </section>

  <a class="subscribe">
    <span class="subscribe-small">SUBSCRIBE TO</span>
    <span class="subscribe-big">PRISM 48 <span>BLOG</span></span>
    <svg class="subscribe-icon" width="40" height="40" viewBox="0 0 40 40">
      <rect width="40" height="40" rx="7" fill="#1e2a06"/>
      <path d="M9 11h22v14H20l-6 5v-5H9z" fill="none" stroke="#eef7c4" stroke-width="2.5" stroke-linejoin="round"/>
    </svg>
  </a>

  <footer class="site-footer">Copyright © 2012 Prism48.All Rights Reserved</footer>
</body>
</html>
```